Logo and Simple Website - Lumo IT

I require a good logo and simple website for an IT trading business. I am uploading the website text and description.
For the logo, I was thinking of something that has a (partial) cube but also looks a bit like a circuit board. The name should be easy to read, but there should also be a graphical element to the logo. The graphical element can be used on its own for tabs or headers on the website. The logo needs to be suitable for business cards and stationery as well.
I am open to color schemes, but perhaps something in purple tones.

Target Market(s)

Corporate clients

Industry/Entity Type

It Professional

Logo Text

Lumo IT

Number of Pages Required

1 page

Font styles to use
Other font styles liked:
• Eurostyle, Futura

Colors

Designer to choose colors to be used in the design.

Requirements
Must have
• Simple, streamlined look, but should not look too basic.

```html
<!DOCTYPE html>
<html lang="en">
<head>
<meta charset="utf-8">
<title>Lumo IT</title>
<link href="https://fonts.googleapis.com/css2?family=Jura:wght@300;400;600&family=Open+Sans:wght@400;600;700&display=swap" rel="stylesheet">
<style>
:root{
  --purple:#6a07c2;
  --purple-deep:#4a0596;
  --purple-text:#5b0aa8;
  --amber:#f7b500;
  --ink:#333;
  --grey-bg:#ebebeb;
  --brand-grey:#9a9a9a;
  --white:#fff;
}
*{margin:0;padding:0;box-sizing:border-box}
html,body{width:1200px;height:3711px;overflow:hidden;background:var(--white)}
body{font-family:"Open Sans",sans-serif;color:var(--ink);position:relative}
.heading{font-family:"Jura",sans-serif;font-weight:400;letter-spacing:1px}

/* hero */
.hero{position:absolute;left:0;top:0;width:1200px;height:650px;background:linear-gradient(135deg,#3a2a52 0%,#5a3f78 40%,#2c2240 100%)}
.hero-edge{position:absolute;left:0;bottom:0;width:1200px;height:30px}
.nav{position:absolute;left:160px;top:30px;width:880px;height:70px;display:flex;align-items:center;justify-content:space-between}
.brand{display:flex;align-items:center;gap:16px;color:var(--white);font-family:"Jura",sans-serif;font-weight:600;font-size:40px}
.brand-mark{width:46px;height:46px;border:3px solid var(--white)}
.menu{display:flex;gap:40px;list-style:none}
.menu li{color:var(--white);font-weight:700;font-size:18px;letter-spacing:.5px}
.hero-title{position:absolute;top:222px;width:1200px;text-align:center;color:var(--white);font-size:58px;letter-spacing:3px;font-weight:300}
.hero-sub{position:absolute;top:296px;width:1200px;text-align:center;color:var(--white);font-family:"Jura",sans-serif;font-size:27px;line-height:32px}
.dots{position:absolute;top:594px;left:563px;display:flex;gap:8px}
.dots span{width:13px;height:13px;border-radius:50%;background:var(--white)}
.dots span:first-child{background:none;border:2px solid var(--white)}

/* section tab marks */
.mark{position:absolute;left:585px;width:30px;height:30px;border:3px solid var(--purple)}
.section-title{position:absolute;width:1200px;text-align:center;color:var(--purple-text);font-size:42px}

/* about */
.about-text{position:absolute;left:195px;top:842px;width:810px;text-align:center;font-size:14px;line-height:22px}
.about-text p{margin-bottom:12px}

/* team */
.team{position:absolute;left:0;top:1180px;width:1200px;height:606px;background:linear-gradient(180deg,#5a07b4 0%,#6a10c8 50%,#4e06a0 100%)}
.team-tab{position:absolute;left:560px;top:1136px;width:80px;height:80px}
.team .section-title{color:var(--white);top:40px}
.team-intro{position:absolute;left:250px;top:103px;width:700px;text-align:center;color:var(--white);font-size:18px;line-height:25px}
.team-intro p{margin-bottom:8px}
.member{position:absolute;top:250px;width:220px;text-align:center;color:var(--white)}
.member svg{display:block;margin:0 auto}
.member-name{margin-top:20px;font-weight:700;font-size:17px;letter-spacing:.5px}
.member-role{font-size:12px;line-height:18px;margin-top:4px;opacity:.9}

/* products */
.products-intro{position:absolute;left:235px;top:1918px;width:730px;text-align:center;font-size:18px;line-height:25px}
.brand-box{position:absolute;left:161px;width:878px;height:181px;border:2px solid var(--purple)}
.box-label{position:absolute;top:-17px;left:50%;transform:translateX(-50%);background:var(--white);padding:0 14px;display:flex;align-items:center;gap:10px;color:var(--purple);font-family:"Jura",sans-serif;font-weight:600;font-size:26px;letter-spacing:1px}
.box-label::before,.box-label::after{content:"";width:9px;height:9px;border-radius:50%;background:var(--purple)}
.brand-row{position:absolute;left:40px;right:40px;top:60px;height:60px;display:flex;justify-content:space-between;align-items:center}
.brand-row span{color:var(--brand-grey);font-weight:600;font-size:26px}

/* services */
.services{position:absolute;left:0;top:2551px;width:1200px;height:497px}
.services-title{position:absolute;left:173px;top:65px;color:var(--white);font-size:40px}
.services-text{position:absolute;left:173px;top:132px;width:360px;color:var(--white);font-size:15.5px;line-height:24px}
.services-text p{margin-bottom:10px}

/* contact */
.contact{position:absolute;left:0;top:3048px;width:1200px;height:569px;background:var(--grey-bg)}
.contact-form{position:absolute;left:161px;top:82px;width:457px;height:403px;background:linear-gradient(160deg,#6308b8,#5005a0)}
.field{position:absolute;left:42px;width:375px;border-bottom:2px solid rgba(255,255,255,.85);color:var(--white);font-size:15px;padding-bottom:6px;letter-spacing:.5px}
.submit{position:absolute;left:42px;top:316px;width:180px;height:50px;background:var(--amber);color:var(--white);font-weight:700;font-size:20px;display:flex;align-items:center;justify-content:center}
.contact-title{position:absolute;left:688px;top:96px;color:var(--purple-text);font-size:36px}
.contact-list{position:absolute;left:691px;top:172px;list-style:none;font-size:16px;font-weight:600;color:#444}
.contact-list li{height:34.8px}
.contact-list .company{color:var(--purple);font-size:19px;font-weight:700}
.social{position:absolute;left:694px;top:405px;display:flex;gap:36px}
.social span{width:20px;height:20px;border-radius:50%;background:var(--purple)}

/* footer */
.footer{position:absolute;top:3638px;width:1200px;text-align:center;font-size:13px;color:#555}
</style>
</head>
<body>

<header class="hero" role="img" aria-label="Photograph of computer memory modules and circuit boards">
  <nav class="nav">
    <div class="brand"><span class="brand-mark"></span>Lumo IT</div>
    <ul class="menu"><li>ABOUT US</li><li>TEAM</li><li>PRODUCTS</li><li>SERVICES</li><li>CONTACT</li></ul>
  </nav>
  <h1 class="hero-title heading">WELCOME TO LUMO IT</h1>
  <p class="hero-sub">CLASS APTENT TACITI SOCIOSQU AD LITORA<br>TORQUENT PER CONUBIA NOSTRA</p>
  <div class="dots"><span></span><span></span><span></span><span></span></div>
  <svg class="hero-edge" viewBox="0 0 1200 30" preserveAspectRatio="none"><path d="M0 14 Q30 4 60 14 T120 12 T180 16 T240 10 T300 15 T360 11 T420 16 T480 12 T540 15 T600 10 T660 16 T720 12 T780 15 T840 11 T900 16 T960 12 T1020 15 T1080 10 T1140 15 T1200 12 V30 H0Z" fill="#fff"/></svg>
</header>

<section class="about">
  <span class="mark" style="top:715px"></span>
  <h2 class="section-title heading" style="top:770px">ABOUT US</h2>
  <div class="about-text">
    <p>We are a specialized IT trading company, with a focus on high end storage solutions. As businesses and individuals continue to generate ever-greater amounts of data, storage technologies need to keep pace. We believe that understanding the needs of our customers puts us in an excellent position to fulfill their requirements in this fast evolving market.</p>
    <p>We operate in the Middle East, Africa and the CIS, and are particularly well suited to the complex dynamics of these markets. We understand the need for cost consciousness and are motivated by a desire to provide first-rate products and professional services to a wide customer base.</p>
    <p>From our logistics hub in Dubai, we are able to provide cost effective and speedy transportation to our customers. We are motivated by the desire to build real partnerships with our customers, and always aim to provide solutions that guarantee profitability for all participants in the value chain.</p>
  </div>
</section>

<section class="team">
  <h2 class="section-title heading">OUR TEAM</h2>
  <div class="team-intro">
    <p>Our team is here to serve you. All of our sales professionals and technical support staff have a passion for information technology, and are dedicated to our customers.</p>
    <p>Our management team comprises individuals with many years of in-depth experience in the storage solutions sector.</p>
  </div>
  <div class="member" style="left:214px">
    <svg width="160" height="180" viewBox="0 0 160 180" role="img" aria-label="Portrait photo of a team member"><polygon points="80,2 158,46 158,134 80,178 2,134 2,46" fill="none" stroke="#fff" stroke-width="3"/><polygon points="80,14 147,52 147,128 80,166 13,128 13,52" fill="#b9a8c9"/></svg>
    <div class="member-name">MEMBER NAME</div>
    <div class="member-role">Class aptent taciti sociosqu ad litora<br>torquent per conubia nos</div>
  </div>
  <div class="member" style="left:496px">
    <svg width="160" height="180" viewBox="0 0 160 180" role="img" aria-label="Portrait photo of a team member"><polygon points="80,2 158,46 158,134 80,178 2,134 2,46" fill="none" stroke="#fff" stroke-width="3"/><polygon points="80,14 147,52 147,128 80,166 13,128 13,52" fill="#a899b8"/></svg>
    <div class="member-name">MEMBER NAME</div>
    <div class="member-role">Class aptent taciti sociosqu ad litora<br>torquent per conubia nos</div>
  </div>
  <div class="member" style="left:778px">
    <svg width="160" height="180" viewBox="0 0 160 180" role="img" aria-label="Portrait photo of a team member"><polygon points="80,2 158,46 158,134 80,178 2,134 2,46" fill="none" stroke="#fff" stroke-width="3"/><polygon points="80,14 147,52 147,128 80,166 13,128 13,52" fill="#c4b6d2"/></svg>
    <div class="member-name">MEMBER NAME</div>
    <div class="member-role">Class aptent taciti sociosqu ad litora<br>torquent per conubia nos</div>
  </div>
</section>
<svg class="team-tab" viewBox="0 0 80 80"><polygon points="40,0 78,20 78,60 40,80 2,60 2,20" fill="#fff"/><rect x="26" y="26" width="28" height="28" fill="none" stroke="#6a07c2" stroke-width="3"/></svg>

<section class="products">
  <span class="mark" style="top:1792px"></span>
  <h2 class="section-title heading" style="top:1852px">PRODUCTS</h2>
  <p class="products-intro">As a high end storage specialist, we trade in memory, as well as Hard Disk Drives and Solid State Drives. Whether it be mass market product ranges, or specialized products, we will be able to source and deliver at the most competitive price.</p>
  <div class="brand-box" style="top:2051px">
    <div class="box-label">MEMORY</div>
    <div class="brand-row"><span>Novaram</span><span>Bitcrest</span><span>Flashwell</span><span>Keystone</span><span>Ravenpeak</span></div>
  </div>
  <div class="brand-box" style="top:2293px">
    <div class="box-label">STORAGE</div>
    <div class="brand-row"><span>Westfield Data</span><span>Seabright</span><span>Hikari</span><span>Tomura</span><span>Fujimar</span></div>
  </div>
</section>

<section class="services">
  <svg width="1200" height="497" viewBox="0 0 1200 497" style="position:absolute;left:0;top:0">
    <defs><linearGradient id="svc" x1="0" y1="0" x2="1" y2="1"><stop offset="0" stop-color="#6a07c2"/><stop offset="1" stop-color="#5604a8"/></linearGradient>
    <linearGradient id="hw" x1="0" y1="0" x2="1" y2="1"><stop offset="0" stop-color="#3b3b3e"/><stop offset=".5" stop-color="#5c5a60"/><stop offset="1" stop-color="#2a2a2d"/></linearGradient></defs>
    <rect width="1200" height="497" fill="url(#svc)"/>
    <polygon points="549,0 1200,0 1200,497 549,497 673,245" fill="url(#hw)" role="img" aria-label="Photograph of hard drives, solid state drives and memory modules"/>
  </svg>
  <h2 class="services-title heading">SERVICES</h2>
  <div class="services-text">
    <p>We are first and foremost a trusted supplier of storage products. In this respect, our strong technical expertise and wide range of experience allows us to consult clients on the best strategy for meeting their data storage needs, coupled with a clear commitment for delivering the products required to execute this.</p>
    <p>We work with blanket orders as required, giving customers the possibility to secure stock and plan ahead without the worry of product shortages or price fluctuations.</p>
  </div>
</section>

<section class="contact">
  <form class="contact-form">
    <div class="field" style="top:38px">NAME</div>
    <div class="field" style="top:92px">EMAIL</div>
    <div class="field" style="top:146px">PHONE NUMBER</div>
    <div class="field" style="top:200px;height:96px">MESSAGE</div>
    <div class="submit">SUBMIT</div>
  </form>
  <h2 class="contact-title heading">CONTACT US</h2>
  <ul class="contact-list">
    <li class="company">LUMO IT FZ-LLC</li>
    <li>HARBOR TRADE ZONE</li>
    <li>UNITED ARAB EMIRATES</li>
    <li>TEL: 600 555 0142</li>
    <li>FAX: 600 555 0187</li>
    <li>CONTACT@LUMOIT.EXAMPLE</li>
  </ul>
  <div class="social" aria-label="Social links"><span></span><span></span><span></span><span></span></div>
</section>

<footer class="footer">© 2019 COMPANY NAME &nbsp;ALL RIGHT RESERVED</footer>

</body>
</html>
```